Business Card Design Project

Doctor, Pain Management. Need a new business card design with appointment info on the back. New address is 18 Corvell Road, Suite 304, Brisdale, NJ 07391. Right now I believe the rest of the information is staying the same.

```html
<!DOCTYPE html>
<html lang="en">
<head>
<meta charset="utf-8">
<title>Business Card – Gentle Relief Pain Care</title>
<link rel="stylesheet" href="https://fonts.googleapis.com/css2?family=Tinos:wght@400;700&family=Open+Sans:ital,wght@0,400;0,700;1,400&display=swap">
<style>
  :root {
    --page-bg: #e9e6e1;
    --sky-light: #a9ddf7;
    --sky: #7ccaf3;
    --panel-black: #1b1c1e;
    --brand-yellow: #e7e14f;
    --ink-dark: #2f3438;
    --ink-soft: #50565b;
    --paper: #ffffff;
    --rule: #8a8f93;
    --shadow: rgba(0,0,0,0.22);
  }
  * { box-sizing: border-box; margin: 0; padding: 0; }
  html, body { width: 1200px; height: 950px; overflow: hidden; background: var(--page-bg); }
  .canvas {
    width: 1200px; height: 950px;
    display: flex; flex-direction: column; align-items: center; justify-content: center; gap: 50px;
  }
  .card {
    position: relative; width: 700px; height: 400px; overflow: hidden;
    box-shadow: 0 6px 18px var(--shadow);
  }

  /* Front */
  .card-front { background: linear-gradient(160deg, var(--sky-light) 0%, var(--sky) 100%); }
  .front-panel { position: absolute; inset: 0; }
  .brand {
    position: absolute; left: 410px; top: 170px;
    display: flex; align-items: center; gap: 10px;
    font-family: "Tinos", serif; font-size: 23px; color: var(--brand-yellow);
    white-space: nowrap;
  }
  .brand-dot { width: 18px; height: 18px; border-radius: 50%; background: var(--brand-yellow); flex: none; }
  .contact {
    position: absolute; left: 36px; bottom: 28px;
    font-family: "Tinos", serif; color: var(--ink-dark);
  }
  .contact-name { font-size: 27px; font-weight: 400; line-height: 1.1; white-space: nowrap; }
  .contact-title { font-size: 17px; margin: 2px 0 6px 14px; color: var(--ink-soft); }
  .contact-lines { margin-left: 28px; font-size: 16px; line-height: 1.3; color: var(--ink-soft); list-style: none; }
  .contact-lines li { display: flex; align-items: center; gap: 8px; white-space: nowrap; }
  .contact-lines svg { width: 13px; height: 13px; fill: var(--ink-dark); flex: none; }

  /* Back */
  .card-back { background: var(--paper); font-family: "Open Sans", sans-serif; color: var(--ink-dark); padding: 34px 44px; }
  .back-title { text-align: center; font-size: 30px; font-weight: 700; margin-bottom: 26px; }
  .field { display: flex; align-items: flex-end; gap: 8px; font-size: 20px; margin-bottom: 20px; }
  .field-line { flex: 1; border-bottom: 2px dotted var(--rule); height: 20px; }
  .field-suffix { font-size: 13px; }
  .days { display: flex; justify-content: space-between; font-size: 19px; margin: 6px 0 30px; }
  .day { display: flex; align-items: center; gap: 5px; }
  .box { width: 17px; height: 17px; border: 1.5px solid var(--ink-dark); }
  .notice { font-style: italic; font-size: 15px; line-height: 1.4; text-align: center; }
</style>
</head>
<body>
<main class="canvas">

  <section class="card card-front" aria-label="Business card front">
    <svg class="front-panel" viewBox="0 0 700 400" aria-hidden="true">
      <path d="M470 0 C350 90 350 330 500 400 L700 400 L700 0 Z" fill="var(--panel-black)"/>
      <path d="M470 0 C350 90 350 330 500 400" fill="none" stroke="#fff" stroke-width="3" stroke-dasharray="4 4"/>
    </svg>
    <div class="brand"><span class="brand-dot"></span><span>Gentle Relief Pain Care</span></div>

    <div class="contact">
      <h1 class="contact-name">Meilan Zhou, M.D., Ph.D.</h1>
      <p class="contact-title">Board Certified Anesthesiologist</p>
      <ul class="contact-lines">
        <li>18 Corvell Road</li>
        <li>Suite 304</li>
        <li>Brisdale, NJ 07391</li>
        <li><svg viewBox="0 0 16 16"><path d="M3 1l3 0 1.5 4-2 1.3a9 9 0 0 0 4.2 4.2L11 8.5l4 1.5v3a2 2 0 0 1-2 2A12 12 0 0 1 1 3a2 2 0 0 1 2-2z"/></svg>973.555.0142</li>
        <li><svg viewBox="0 0 16 16"><path d="M4 1h8v4H4zM1 6h14v7h-3v2H4v-2H1zM5 10v4h6v-4z"/></svg>973.555.0187</li>
        <li><svg viewBox="0 0 16 16"><path d="M1 3h14v10H1zM2.5 4.5 8 9l5.5-4.5z" fill-rule="evenodd"/></svg>gentlerelief.office@mailbox.com</li>
        <li><svg viewBox="0 0 16 16"><circle cx="8" cy="8" r="7"/></svg>www.gentlereliefpc.com</li>
      </ul>
    </div>
  </section>

  <section class="card card-back" aria-label="Business card back">
    <h2 class="back-title">Next Appointment</h2>
    <div class="field"><span>Name :</span><span class="field-line"></span></div>
    <div class="field"><span>Date :</span><span class="field-line"></span><span>Time :</span><span class="field-line"></span><span class="field-suffix">AM/PM</span></div>
    <div class="days">
      <span class="day">Mon<span class="box"></span></span>
      <span class="day">Tue<span class="box"></span></span>
      <span class="day">Wed<span class="box"></span></span>
      <span class="day">Thu<span class="box"></span></span>
      <span class="day">Fri<span class="box"></span></span>
      <span class="day">Sat<span class="box"></span></span>
    </div>
    <p class="notice">Please give 24 hours notice if you are unable to keep your appointment or<br>a cancellation fee may be charged.</p>
  </section>

</main>
</body>
</html>
```